real esate business card with company logo and name

we need a business card design for a real esate company

The company name is Walsh & Brand Pty Ltd, and we have our logo designed and will upload. We want classic or moden feel. Black or white background. looks more textured. Should include folowinginformations
Owen Walsh and Lucy Brand
Sales Agents & Onsite Manager
p: 07 5948 2063
F: 07 5948 2174
M:0431 857 219
3/42 Marlow Crescent, FERNLEA QLD 4213

We want this business card looks professonal. Thank you in advance.

Industry/Entity Type

Real Estate Agent

Contact Information for Business Card

Owen Walsh and Lucy Brand
Onsite Manager & Sales Agents
p: 07 5948 2063
M:0431 857 219

Font styles to use
Serif

Colors
000000
fbfbfb
333333
959595

Requirements
Must have
• company logo and name, black or white back ground

```html
<!DOCTYPE html>
<html lang="en">
<head>
<meta charset="utf-8">
<title>Walsh &amp; Brand Pty Ltd – Business Card</title>
<link rel="stylesheet" href="https://fonts.googleapis.com/css2?family=Montserrat:wght@600&family=Roboto+Condensed:wght@300;400&display=swap">
<style>
  :root {
    --page-bg: #cfcfcf;
    --card-bg-top: #f1f1f1;
    --card-bg-bottom: #e2e2e2;
    --ink-dark: #333333;
    --panel-dark: #1e1e1e;
    --panel-edge: #000000;
    --panel-line: #959595;
    --text-light: #fbfbfb;
    --text-muted: #d6d6d6;
    --text-accent: #c4b493;
  }
  html, body {
    margin: 0;
    padding: 0;
    width: 1200px;
    height: 969px;
    overflow: hidden;
    background: var(--page-bg);
  }
  .card {
    position: absolute;
    left: 90px;
    top: 196px;
    width: 1020px;
    height: 576px;
    background: linear-gradient(160deg, var(--card-bg-top), var(--card-bg-bottom));
    box-shadow: 0 10px 30px rgba(0,0,0,0.18);
    overflow: hidden;
  }
  .brand-mark {
    position: absolute;
    left: 128px;
    top: 78px;
    width: 196px;
    height: 196px;
    background: var(--ink-dark);
  }
  .brand-name {
    position: absolute;
    left: 40px;
    top: 346px;
    width: 372px;
    text-align: center;
    font-family: "Montserrat", sans-serif;
    font-weight: 600;
    font-size: 24px;
    letter-spacing: 0.5px;
    color: var(--ink-dark);
    white-space: nowrap;
  }
  .contact-panel {
    position: absolute;
    left: 0;
    top: 0;
    width: 1020px;
    height: 576px;
  }
  .contact {
    position: absolute;
    left: 612px;
    top: 284px;
    width: 350px;
    font-family: "Roboto Condensed", sans-serif;
    text-align: right;
  }
  .contact-names {
    margin: 0;
    font-weight: 400;
    font-size: 31px;
    line-height: 40px;
    color: var(--text-muted);
    text-align: left;
    white-space: nowrap;
  }
  .contact-role {
    margin: 0 0 14px;
    font-weight: 400;
    font-size: 22px;
    line-height: 32px;
    color: var(--text-accent);
    text-align: left;
    white-space: nowrap;
  }
  .contact-line {
    display: flex;
    justify-content: flex-end;
    align-items: center;
    gap: 10px;
    margin: 0;
    font-weight: 400;
    font-size: 22px;
    line-height: 38px;
    color: var(--text-light);
  }
  .contact-line svg { width: 22px; height: 22px; fill: var(--text-light); }
  .address {
    margin: 8px 32px 0 0;
    font-weight: 300;
    font-size: 22px;
    line-height: 30px;
    color: var(--text-muted);
  }
  .address .suburb { display: block; color: var(--text-accent); }
</style>
</head>
<body>
  <section class="card" aria-label="Walsh &amp; Brand business card">
    <div class="brand-mark"></div>
    <div class="brand-name">WALSH &amp; BRAND PTY LTD.</div>

    <svg class="contact-panel" viewBox="0 0 1020 576" aria-hidden="true">
      <polygon points="504,576 504,268 723,158 1020,268 1020,576" fill="var(--panel-edge)"/>
      <polygon points="512,576 512,273 723,167 1020,276 1020,576" fill="none" stroke="var(--panel-line)" stroke-width="2"/>
      <polygon points="520,576 520,278 723,176 1020,284 1020,576" fill="var(--panel-dark)"/>
    </svg>

    <div class="contact">
      <p class="contact-names">Owen Walsh &amp; Lucy Brand</p>
      <p class="contact-role">Sales Agents &amp; Onsite Manager</p>
      <p class="contact-line">07 5948 2063
        <svg viewBox="0 0 24 24" aria-label="phone"><path d="M6.6 10.8a15.1 15.1 0 0 0 6.6 6.6l2.2-2.2a1 1 0 0 1 1-.25 11.4 11.4 0 0 0 3.6.57 1 1 0 0 1 1 1V20a1 1 0 0 1-1 1A17 17 0 0 1 3 4a1 1 0 0 1 1-1h3.5a1 1 0 0 1 1 1c0 1.25.2 2.45.57 3.57a1 1 0 0 1-.25 1z"/></svg>
      </p>
      <p class="contact-line">0431 857 219
        <svg viewBox="0 0 24 24" aria-label="mobile"><path d="M7 1h10a2 2 0 0 1 2 2v18a2 2 0 0 1-2 2H7a2 2 0 0 1-2-2V3a2 2 0 0 1 2-2zm0 3v14h10V4zm5 15.5a1 1 0 1 0 0 2 1 1 0 0 0 0-2z"/></svg>
      </p>
      <p class="contact-line">07 5948 2174
        <svg viewBox="0 0 24 24" aria-label="fax"><path d="M7 2h8l3 3v5H7zm-3 9h16a2 2 0 0 1 2 2v7a2 2 0 0 1-2 2H4a2 2 0 0 1-2-2v-7a2 2 0 0 1 2-2zm2 3v2h3v-2zm5 0v2h3v-2zm5 0v2h3v-2zm-10 4v2h3v-2zm5 0v2h3v-2z"/></svg>
      </p>
      <p class="address">3/42 Marlow Crescent<span class="suburb">FERNLEA QLD 4213</span></p>
    </div>
  </section>
</body>
</html>
```